Building company buisness cards

We are looking for a sharp modern new look for our business cards.We are a New Zealand based company that specialises in house and land packages.We have attached a photo of the current logo and would like to see if it can be improved somehow if needed.We are open to any colours but we have chosen Black and White at this stage. Feel free to change the font and make the logo smarter looking.Play with the colours and see what looks best.We want a card that looks so good know one will want to throw it away!

Target Market(s)

Building profesonals, home buyers

Industry/Entity Type

Building

Contact Information for Business Card

Garrick Tenwood
0275390628
garrickt@hartvale.co.nz

Font styles to use
Serif
Sans Serif

Colors

Designer to choose colors to be used in the design.

Requirements
Must have
• Just the logo on one side and details on the other
• Clean simple looking card
Nice to have
• Round corners and detail like raised or spot UV
• Something that stands out
Should not have
• To title needed, Director etc

```html
<!DOCTYPE html>
<html lang="en">
<head>
<meta charset="utf-8">
<title>Hartvale Business Card</title>
<link rel="stylesheet" href="https://fonts.googleapis.com/css2?family=Playfair+Display:wght@700;900&family=Roboto:wght@400&display=swap">
<style>
  :root {
    --page-bg: #e6e6e6;
    --card-white: #ffffff;
    --ink: #0c0c0e;
    --text-grey: #4a4a4a;
    --back-dark: #0b0b0d;
    --back-mid: #1a1b1f;
    --reverse: #ffffff;
  }
  * { margin: 0; padding: 0; box-sizing: border-box; }
  html, body {
    width: 1125px;
    height: 1200px;
    overflow: hidden;
    background: var(--page-bg);
  }
  .card {
    position: absolute;
    left: 171px;
    width: 826px;
    height: 470px;
    border-radius: 20px;
    overflow: hidden;
  }
  .card-front { top: 106px; background: var(--card-white); }
  .card-back { top: 640px; background: var(--back-dark); }

  .brand {
    position: absolute;
    left: 42px;
    top: 62px;
    display: flex;
    align-items: center;
    gap: 18px;
  }
  .brand-name {
    font-family: "Playfair Display", serif;
    font-weight: 900;
    font-size: 92px;
    line-height: 1;
    color: var(--ink);
    letter-spacing: -1px;
  }
  .brand-ring {
    width: 92px;
    height: 92px;
    border: 3px solid var(--ink);
    border-radius: 50%;
  }

  .edge-dot {
    position: absolute;
    left: -26px;
    top: 304px;
    width: 44px;
    height: 44px;
    border-radius: 50%;
    background: var(--ink);
  }
  .holder-name {
    position: absolute;
    left: 42px;
    top: 305px;
    font-family: "Playfair Display", serif;
    font-weight: 700;
    font-size: 27px;
    letter-spacing: 0.5px;
    text-transform: uppercase;
    color: var(--ink);
  }
  .name-rule {
    position: absolute;
    left: 42px;
    top: 344px;
    width: 740px;
    height: 1.5px;
    background: var(--ink);
  }
  .contact-list {
    position: absolute;
    left: 42px;
    top: 380px;
    list-style: none;
    font-family: "Roboto", sans-serif;
    font-size: 19px;
    color: var(--text-grey);
  }
  .contact-list li {
    display: flex;
    align-items: center;
    gap: 10px;
    height: 27px;
  }
  .contact-list svg { width: 19px; height: 19px; fill: var(--ink); }
  .website {
    position: absolute;
    right: 44px;
    top: 408px;
    font-family: "Roboto", sans-serif;
    font-size: 19px;
    color: var(--text-grey);
  }

  .back-texture {
    position: absolute;
    inset: 0;
    background: linear-gradient(135deg, var(--back-mid) 0%, var(--back-dark) 55%, #121317 100%);
  }
  .back-mark {
    position: absolute;
    display: flex;
    align-items: center;
    gap: 12px;
  }
  .back-mark-top { left: 30px; top: 67px; }
  .back-mark-bottom { right: 30px; top: 328px; }
  .back-ring {
    width: 68px;
    height: 68px;
    border: 3px solid var(--reverse);
    border-radius: 50%;
  }
  .back-name {
    font-family: "Playfair Display", serif;
    font-weight: 900;
    font-size: 26px;
    color: var(--reverse);
  }
</style>
</head>
<body>

<section class="card card-front" aria-label="Business card front">
  <div class="brand">
    <span class="brand-name">Hartvale</span>
    <span class="brand-ring" aria-hidden="true"></span>
  </div>

  <span class="edge-dot" aria-hidden="true"></span>
  <h1 class="holder-name">Garrick Tenwood</h1>
  <div class="name-rule" aria-hidden="true"></div>

  <ul class="contact-list">
    <li>
      <svg viewBox="0 0 24 24" aria-hidden="true"><path d="M6.6 10.8a15.1 15.1 0 0 0 6.6 6.6l2.2-2.2c.3-.3.7-.4 1-.2 1.1.4 2.3.6 3.6.6.6 0 1 .4 1 1V20c0 .6-.4 1-1 1A17 17 0 0 1 3 4c0-.6.4-1 1-1h3.5c.6 0 1 .4 1 1 0 1.3.2 2.5.6 3.6.1.3 0 .7-.2 1z"/></svg>
      <span>0275390628</span>
    </li>
    <li>
      <svg viewBox="0 0 24 24" aria-hidden="true"><path d="M2 6h20v12H2z" fill="none" stroke="#0c0c0e" stroke-width="2"/><path d="M2 6l10 7 10-7" fill="none" stroke="#0c0c0e" stroke-width="2"/></svg>
      <span>garrickt@hartvale.co.nz</span>
    </li>
  </ul>
  <p class="website">www.hartvale.co.nz</p>
</section>

<section class="card card-back" aria-label="Business card back">
  <div class="back-texture" role="img" aria-label="Tone-on-tone repeating brand pattern across the dark card back"></div>
  <div class="back-mark back-mark-top">
    <span class="back-ring" aria-hidden="true"></span>
    <span class="back-name">Hartvale</span>
  </div>
  <div class="back-mark back-mark-bottom">
    <span class="back-name">Hartvale</span>
    <span class="back-ring" aria-hidden="true"></span>
  </div>
</section>

</body>
</html>
```